BRIVAN 2026 Flyer for Conference

BRIVAN needs a design for a 1-page flyer that we will hand out at an upcoming event & then later post online as a pdf. There are 3 elements which need to be on the flyer:

1) A logo. This should be prominent on the design (e.g., in the middle). The flyer should use the colors that are in that logo (e.g., for accents, design elements, and/or text; not all of these have to be used):
Dark blue: #185577
Med blue: #327C9A
Teal: #4EB1C2
Light Teal: #9EDBE6

2) The conference theme -- Oceans of Knowledge: Diving into Information Literacy -- should be at the flyer's top.

3) Finally, these six tracks should be listed below the theme and the logo (it's font size should be at least a couple sizes smaller than the size used for the theme):
- Pearls of Pedagogy: Teaching Techniques that Work
- The Depth Gauge: Measuring Instructional Impact
- Techtonic Shifts: Innovation and Educational Technology
- Captain's Log: Navigating Leadership in Library Instruction
- Swimming Together: Collaborating with Others
- The Bermuda Triangle: Exploring (Seemingly) Eternal Challenges

Font styles to use
Sans Serif

Colors
0094D4
00A9DD
6FCCEA
C7EBF8
E9F6FB

Requirements
Must have
• The 3 elements listed in the description: 1) the logo, 2) the text of the theme and 3) the text for the tracks.

```html
<!DOCTYPE html>
<html lang="en">
<head>
<meta charset="utf-8">
<title>BRIVAN 2026 – Oceans of Knowledge</title>
<link href="https://fonts.googleapis.com/css2?family=Poppins:wght@400;500;600;700;800&display=swap" rel="stylesheet">
<style>
  :root {
    --page-bg: #e6ebee;
    --paper: #f3f3f2;
    --navy: #28496a;
    --deep: #2e4f70;
    --mid: #4d7896;
    --teal: #5f9fb4;
    --light-teal: #9ecfdc;
  }
  * { margin: 0; padding: 0; box-sizing: border-box; }
  html, body {
    width: 1200px; height: 801px; overflow: hidden;
    background: var(--page-bg);
    font-family: "Poppins", sans-serif;
  }
  .flyer {
    position: absolute; left: 322px; top: 0;
    width: 556px; height: 801px;
    background: var(--paper);
    overflow: hidden;
  }
  .sea-scene {
    position: absolute; inset: 0;
    width: 556px; height: 801px;
  }
  .content {
    position: absolute; left: 24px; top: 0; width: 290px;
  }
  .brand {
    margin-top: 70px;
    display: flex; align-items: center; gap: 10px;
  }
  .brand-dot {
    width: 26px; height: 26px; border-radius: 50%;
    background: var(--teal);
  }
  .brand-name {
    font-size: 38px; font-weight: 700; color: var(--navy);
    letter-spacing: 0.5px; line-height: 1;
  }
  .brand-place {
    margin-top: 10px; margin-left: 36px;
    font-size: 10px; font-weight: 500; letter-spacing: 2px;
    color: var(--teal); text-transform: uppercase;
  }
  .theme {
    margin-top: 48px;
    font-size: 31px; font-weight: 800; line-height: 1.18;
    letter-spacing: 2.5px; text-transform: uppercase;
  }
  .theme-line1 { color: var(--mid); display: block; }
  .theme-line2 { color: var(--navy); display: block; }
  .subtitle {
    margin-top: 8px;
    font-size: 21px; font-weight: 500; line-height: 1.3;
    color: var(--mid);
  }
  .tracks { list-style: none; margin-top: 24px; }
  .track {
    display: flex; align-items: center; gap: 10px;
    height: 75px;
  }
  .track-icon {
    flex: 0 0 26px; height: 18px; border-radius: 50%;
    background: var(--teal);
  }
  .track-title {
    font-size: 14.5px; font-weight: 600; color: var(--navy); line-height: 1.25;
  }
  .track-desc {
    font-size: 14.5px; font-weight: 400; color: var(--teal); line-height: 1.3;
  }
</style>
</head>
<body>
  <main class="flyer">
    <svg class="sea-scene" viewBox="0 0 556 801" role="img" aria-label="Layered paper-cut underwater scene with coral, fish and a sea turtle">
      <defs>
        <linearGradient id="seaGradient" x1="0" y1="0" x2="1" y2="0">
          <stop offset="0" stop-color="#6fa9bb"/>
          <stop offset="0.35" stop-color="#4b7591"/>
          <stop offset="1" stop-color="#2d4d6c"/>
        </linearGradient>
      </defs>
      <path fill="url(#seaGradient)" d="M292,0 C320,40 352,80 342,118 C332,165 276,200 282,252 C288,310 336,345 322,395 C308,445 262,470 272,520 C282,575 330,600 318,650 C306,700 262,720 278,801 L556,801 L556,0 Z"/>
    </svg>

    <div class="content">
      <div class="brand">
        <span class="brand-dot"></span>
        <span class="brand-name">BRIVAN 2026</span>
      </div>
      <p class="brand-place">Port Calder, VA • May 7-9</p>

      <h1 class="theme">
        <span class="theme-line1">Oceans of</span>
        <span class="theme-line2">Knowledge:</span>
      </h1>
      <p class="subtitle">Diving into<br>Information Literacy</p>

      <ul class="tracks">
        <li class="track"><span class="track-icon" role="img" aria-label="Small sea turtle icon"></span>
          <div><p class="track-title">Pearls of Pedagogy:</p><p class="track-desc">Teaching Techniques<br>that Work</p></div></li>
        <li class="track"><span class="track-icon" role="img" aria-label="Small sea turtle icon"></span>
          <div><p class="track-title">The Depth Gauge:</p><p class="track-desc">Measuring Instructional<br>Impact</p></div></li>
        <li class="track"><span class="track-icon" role="img" aria-label="Small sea turtle icon"></span>
          <div><p class="track-title">Techtonic Shifts:</p><p class="track-desc">Innovation and<br>Educational Technology</p></div></li>
        <li class="track"><span class="track-icon" role="img" aria-label="Small sea turtle icon"></span>
          <div><p class="track-title">Captain's Log:</p><p class="track-desc">Navigating Leadership<br>in Library Instruction</p></div></li>
        <li class="track"><span class="track-icon" role="img" aria-label="Small sea turtle icon"></span>
          <div><p class="track-title">Swimming Together:</p><p class="track-desc">Collaborating with<br>Others</p></div></li>
        <li class="track"><span class="track-icon" role="img" aria-label="Small sea turtle icon"></span>
          <div><p class="track-title">The Bermuda Triangle:</p><p class="track-desc">Exploring (Seemingly)<br>Eternal Challenges</p></div></li>
      </ul>
    </div>
  </main>
</body>
</html>
```